IT Company requires new Business Card design.

Over the years we have had a few different business card designs. We are now due for new cards across the board for all staff. We felt this would be a good time to start fresh with a new design. Our traditional card simply had our details on the front, and a list of services on the back. We don't particularly need the list of services, we have had cards where the only thing on the rear of the card was our logo.
Feel free to be creative, we would like our tag line "Complete IT Management" to appear at some point, doesn't necessarily have to be with the logo.
I have attached samples and drafts of various previous cards we have used over the years.

```html
<!DOCTYPE html>
<html lang="en">
<head>
<meta charset="utf-8">
<title>Brook Networking – Business Card</title>
<link rel="stylesheet" href="https://fonts.googleapis.com/css2?family=Source+Sans+3:wght@400;600;700&display=swap">
<style>
  :root {
    --slate: #5f7282;
    --paper: #ffffff;
    --backdrop: #e9e7e4;
    --ink: #4a4a4a;
  }
  * { margin: 0; padding: 0; box-sizing: border-box; }
  html, body {
    width: 1200px; height: 992px; overflow: hidden;
    background: var(--backdrop);
    font-family: "Source Sans 3", sans-serif;
  }
  .card {
    position: absolute;
    width: 502px; height: 878px;
    box-shadow: 0 2px 8px rgba(0,0,0,0.25);
  }
  /* Front */
  .card-front { left: 84px; top: 47px; background: var(--paper); }
  .name-band {
    height: 54px; background: var(--slate);
    color: var(--paper);
    display: flex; align-items: center; justify-content: center;
    font-size: 19px;
  }
  .name-band .person { font-weight: 700; font-size: 25px; margin-right: 7px; }
  .rule {
    position: absolute; left: 0; right: 0; height: 3px; background: var(--slate);
  }
  .rule-top { top: 60px; }
  .rule-bottom { bottom: 67px; }
  .brand {
    position: absolute; left: 0; right: 0; top: 322px;
    display: flex; align-items: center; justify-content: center; gap: 18px;
    color: var(--slate);
  }
  .brand-square { width: 80px; height: 80px; background: var(--slate); }
  .brand-name {
    font-weight: 700; font-size: 44px; line-height: 0.95;
    text-transform: uppercase; letter-spacing: 0.5px;
  }
  .contacts {
    position: absolute; left: 0; right: 0; top: 580px;
    text-align: center; color: var(--ink); font-size: 21px; line-height: 36px;
  }
  .contact-row { display: flex; justify-content: center; align-items: center; gap: 8px; }
  .contact-row .gap { width: 16px; }
  .icon { width: 18px; height: 18px; fill: var(--ink); flex: none; }
  .icon-line { fill: none; stroke: var(--ink); stroke-width: 1.5; }
  .address { margin-top: 20px; }
  .tagline-band {
    position: absolute; left: 0; right: 0; bottom: 0; height: 60px;
    background: var(--slate); color: var(--paper);
    display: flex; align-items: center; justify-content: center;
    font-size: 22px; letter-spacing: 4px; text-transform: uppercase;
  }
  /* Back */
  .card-back { left: 622px; top: 54px; background: var(--slate); color: var(--paper); }
  .back-brand {
    position: absolute; left: 0; right: 0; top: 368px;
    text-align: center; font-weight: 700; font-size: 68px; line-height: 1;
    text-transform: uppercase;
  }
  .back-url {
    position: absolute; left: 0; right: 0; bottom: 38px;
    text-align: center; font-size: 25px; letter-spacing: 1.5px;
  }
  .back-url strong { font-weight: 700; }
</style>
</head>
<body>
  <section class="card card-front">
    <div class="name-band"><span class="person">Mark Ellison,</span> Operation Manager</div>
    <div class="rule rule-top"></div>

    <div class="brand">
      <div class="brand-square"></div>
      <div class="brand-name">Brook<br>Networking</div>
    </div>

    <div class="contacts">
      <div class="contact-row">
        <svg class="icon" viewBox="0 0 20 20"><circle cx="10" cy="10" r="9" fill="none" stroke="#4a4a4a" stroke-width="1.6"/><path d="M7 5c1 0 1.5 2 1.2 2.6L7.5 8.4c.6 1.6 1.9 3 3.6 3.7l.8-.8c.6-.3 2.6.3 2.6 1.3 0 1-1 1.9-2 1.9C8.6 14.5 5.5 11.4 5.5 7 5.5 6 6 5 7 5z"/></svg>
        <span>08 5550 1420</span><span class="gap"></span>
        <svg class="icon" viewBox="0 0 20 20"><rect x="5" y="1" width="10" height="18" rx="1.5"/><rect x="7" y="3.5" width="6" height="5" fill="#fff"/><rect x="7" y="10.5" width="6" height="6" fill="#fff" opacity=".5"/></svg>
        <span>0400 555 218</span>
      </div>
      <div class="contact-row">
        <svg class="icon" viewBox="0 0 20 20"><rect x="5" y="2" width="10" height="6"/><rect x="2" y="8" width="16" height="8" rx="1.5"/><rect x="5" y="12" width="10" height="6" fill="#fff" stroke="#4a4a4a" stroke-width="1.4"/></svg>
        <span>08 5550 1420</span>
      </div>
      <div class="contact-row">
        <svg class="icon" viewBox="0 0 20 20"><path d="M1 8l9-6 9 6v10H1z"/><path d="M3 8l7 5 7-5" fill="none" stroke="#fff" stroke-width="1.4"/></svg>
        <span>mark@brooknetworking.com.au</span>
      </div>
      <div class="contact-row">
        <svg class="icon icon-line" viewBox="0 0 20 20"><circle cx="10" cy="10" r="8.5"/><ellipse cx="10" cy="10" rx="3.8" ry="8.5"/><path d="M1.5 10h17M3 5.5h14M3 14.5h14"/></svg>
        <span>www.brooknetworking.com.au</span>
      </div>
      <div class="address">Unit 7 22 Marlin Court, Bayside WA 6100</div>
    </div>

    <div class="rule rule-bottom"></div>
    <div class="tagline-band">Complete IT Management</div>
  </section>

  <section class="card card-back">
    <div class="back-brand">Brook<br>Networking</div>
    <div class="back-url">www.<strong>brooknetworking</strong>.com.au</div>
  </section>
</body>
</html>
```